BrivoTerna. Lantern of the Steady Harvest. Business card

Professional business card for BrivoTerna (Lantern of the Steady Harvest)
My rationale: Strategy-> Execution-> Results-> Value that lead to the BrivoTerna name: We put the Lantern of the Steady Harvest.
We deliver value to our customers helping them at defining a good strategy (cyan arrow). 90% of well formulated strategies fail due to poor execution so we also consider strategical execution very important (green arrow). Due to the execution we obtain the results (blue arrow). Finally, the results provide feedback to redefine strategy, and the new strategy has to be executed and new results obtained providing new feedback and on and on. It's like a wheel that finally, must create corporate value: value for shareholders, staholders, employees, providers...-

Target Market(s)

CEOs and steering comitees , invewrnent funds

Industry/Entity Type

Business Consultant

Contact Information for Business Card

Teodoro Vinsquel
CEO & Founder
teodoro.vinsquel@brivoterna-example.com
Mobile: +34 655.803.912
www.brivoterna-example.com

Colors

Designer to choose colors to be used in the design.

Requirements
Nice to have
• Nice to hace the words: Strategy, execution, results
• Nice to vave the claim: Lantern of the Steady Harvest
• The three colors should be shown:
• cyan for STRATEGY
• green for EXECUTION
• blue for RESULTS
Should not have
• Complete black background

```html
<!DOCTYPE html>
<html lang="en">
<head>
<meta charset="utf-8">
<title>BrivoTerna – Business Card</title>
<link rel="stylesheet" href="https://fonts.googleapis.com/css2?family=Montserrat:wght@400;500;700;800&display=swap">
<style>
  :root {
    --page-bg: #1c1c1e;
    --royal-blue: #0b2fa8;
    --royal-blue-light: #1740c4;
    --card-dark: #252525;
    --card-dark-edge: #1d1d1d;
    --cyan: #0aa6e8;
    --green: #8cc63f;
    --white: #ffffff;
    --text-light: #e6e6e6;
  }
  * { box-sizing: border-box; margin: 0; padding: 0; }
  html, body { width: 1200px; height: 852px; overflow: hidden; }
  body {
    background: var(--page-bg);
    font-family: "Montserrat", sans-serif;
    position: relative;
  }
  .card {
    position: absolute;
    top: 266px;
    width: 560px;
    height: 320px;
    border-radius: 22px;
    overflow: hidden;
  }
  /* Front */
  .card-front {
    left: 20px;
    background: linear-gradient(135deg, var(--royal-blue) 0%, var(--royal-blue-light) 100%);
  }
  .front-brand {
    position: absolute;
    left: 64px;
    top: 168px;
    display: flex;
    align-items: center;
    gap: 14px;
  }
  .brand-dot {
    width: 22px; height: 22px;
    border-radius: 50%;
    background: var(--green);
  }
  .brand-name {
    font-weight: 800;
    font-size: 44px;
    color: var(--white);
    letter-spacing: -0.5px;
  }
  /* Back */
  .card-back {
    left: 620px;
    background: linear-gradient(135deg, var(--card-dark) 0%, var(--card-dark-edge) 100%);
  }
  .back-brand {
    position: absolute;
    left: 40px;
    top: 70px;
    display: flex;
    align-items: center;
    gap: 10px;
  }
  .back-brand .brand-name { font-size: 32px; }
  .back-brand .brand-dot { width: 16px; height: 16px; }
  .holder {
    position: absolute;
    right: 44px;
    top: 30px;
    text-align: right;
  }
  .holder-name {
    font-weight: 700;
    font-size: 24px;
    color: var(--cyan);
  }
  .holder-title {
    font-weight: 400;
    font-size: 13px;
    color: var(--text-light);
    margin-top: 2px;
  }
  .name-tab {
    position: absolute;
    right: 14px;
    top: 32px;
    width: 16px;
    height: 32px;
    background: var(--green);
  }
  .rule {
    position: absolute;
    height: 1px;
    background: var(--green);
  }
  .rule-top { left: 260px; right: 30px; top: 102px; }
  .rule-contact { left: 36px; width: 300px; top: 190px; }
  .contacts {
    position: absolute;
    left: 40px;
    top: 204px;
    list-style: none;
  }
  .contacts li {
    display: flex;
    align-items: center;
    gap: 10px;
    font-size: 13px;
    color: var(--text-light);
    line-height: 22px;
  }
  .contacts svg { width: 12px; height: 12px; flex: none; }
  .stripe {
    position: absolute;
    bottom: 0;
    height: 14px;
  }
  .stripe-strategy { left: 0; width: 62%; background: var(--cyan); }
  .stripe-execution { right: 0; width: 38%; background: var(--green); }
</style>
</head>
<body>
  <section class="card card-front">
    <div class="front-brand">
      <span class="brand-dot"></span>
      <span class="brand-name">BrivoTerna</span>
    </div>
  </section>

  <section class="card card-back">
    <div class="back-brand">
      <span class="brand-dot"></span>
      <span class="brand-name">BrivoTerna</span>
    </div>

    <div class="holder">
      <p class="holder-name">Teodoro Vinsquel</p>
      <p class="holder-title">CEO &amp; Founder</p>
    </div>
    <span class="name-tab"></span>
    <span class="rule rule-top"></span>

    <span class="rule rule-contact"></span>
    <ul class="contacts">
      <li>
        <svg viewBox="0 0 24 24" aria-hidden="true"><path fill="#0aa6e8" d="M6.6 10.8a15 15 0 0 0 6.6 6.6l2.2-2.2a1 1 0 0 1 1-.25 11.4 11.4 0 0 0 3.6.57 1 1 0 0 1 1 1V20a1 1 0 0 1-1 1A17 17 0 0 1 3 4a1 1 0 0 1 1-1h3.5a1 1 0 0 1 1 1c0 1.25.2 2.45.57 3.6a1 1 0 0 1-.25 1z"/></svg>
        +34 655.803.912
      </li>
      <li>
        <svg viewBox="0 0 24 24" aria-hidden="true"><rect x="2" y="5" width="20" height="14" rx="2" fill="none" stroke="#0aa6e8" stroke-width="2"/><path d="M3 6l9 7 9-7" fill="none" stroke="#0aa6e8" stroke-width="2"/></svg>
        teodoro.vinsquel@brivoterna-example.com
      </li>
      <li>
        <svg viewBox="0 0 24 24" aria-hidden="true"><circle cx="12" cy="12" r="10" fill="none" stroke="#0aa6e8" stroke-width="2"/><path d="M2 12h20M12 2c3 3 3 17 0 20M12 2c-3 3-3 17 0 20" fill="none" stroke="#0aa6e8" stroke-width="2"/></svg>
        www.brivoterna-example.com
      </li>
    </ul>

    <span class="stripe stripe-strategy"></span>
    <span class="stripe stripe-execution"></span>
  </section>
</body>
</html>
```